Business Landing Page for SEO Company

Need the landing page of the website designed - I will provide the copy, will need to include details of my company and the services offered, about us, testimonials, faq, etc., and all these elements will need to be arranged graphically on the page.

I want something similar to this: https://torvanequill.com/

Not in terms of color or theme or anything, but we offer a similar service and want to display similar information.

Th services we provide are:

Premium Links
Monthly Links Subscription
Link Insertions

Need to advertise them on the front page. Additionally need a place for testimonials, company details, etc.,

We already have logo for the website. Please use the attached file to insert the logo within the overal design.

Target Market(s)

SEO marketers and agencies

Number of Pages Required

1 page

```html
<!DOCTYPE html>
<html lang="en">
<head>
<meta charset="utf-8">
<title>quillink – Link Building for SEO Agencies</title>
<link href="https://fonts.googleapis.com/css2?family=Ubuntu:wght@400;500;700&family=Open+Sans:wght@400;600;700&display=swap" rel="stylesheet">
<style>
:root{
  --blue:#1e7be0;
  --blue-deep:#0d4fb0;
  --navy:#031634;
  --orange:#f7931e;
  --orange-deep:#ef7a12;
  --ink:#2c3440;
  --muted:#6b7480;
  --pale:#eef3f8;
  --line:#d6dde6;
  --white:#ffffff;
}
*{box-sizing:border-box;margin:0;padding:0}
html,body{width:1200px;height:4828px;overflow:hidden}
body{position:relative;font-family:"Open Sans",Arial,sans-serif;color:var(--ink);background:var(--white)}
.abs{position:absolute}
h1,h2,h3,.brand{font-family:"Ubuntu",Arial,sans-serif}
.brand{font-weight:700;color:var(--white);font-size:38px;letter-spacing:-.5px}
.accent{color:var(--orange)}
.section-title{position:absolute;left:0;width:1200px;text-align:center;font-size:42px;font-weight:500;color:var(--blue)}

/* hero */
.hero{left:0;top:0;width:1200px;height:800px;overflow:hidden}
.hero-art{position:absolute;inset:0;background:radial-gradient(ellipse 380px 420px at 600px 330px,#2a78d8 0%,#0e3a86 45%,var(--navy) 100%)}
.hero-curve{position:absolute;left:0;top:560px}
.nav{position:absolute;left:60px;top:24px;width:1080px;display:flex;justify-content:space-between;align-items:center}
.nav ul{display:flex;gap:38px;list-style:none}
.nav a{color:var(--white);font-size:13px;font-weight:600;text-decoration:none;letter-spacing:.3px}
.hero-kicker{position:absolute;top:268px;width:1200px;text-align:center;color:var(--white);font-size:30px;font-family:"Ubuntu",sans-serif}
.hero-title{position:absolute;top:302px;width:1200px;text-align:center;color:var(--white);font-size:108px;font-weight:700;letter-spacing:-1px}
.btn{display:inline-block;background:var(--orange);color:var(--white);font-weight:700;font-size:14px;border-radius:24px;padding:12px 30px;text-decoration:none}
.hero .btn{position:absolute;left:526px;top:434px}

/* services */
.service{position:absolute;border-radius:50%;color:var(--white);text-align:center;padding-top:78px}
.service.blue{background:var(--blue);width:320px;height:320px}
.service.orange{background:var(--orange);width:370px;height:370px;padding-top:90px}
.service svg{display:block;margin:0 auto 18px}
.service h3{font-size:25px;font-weight:500;margin-bottom:10px}
.service p{font-size:13px;line-height:1.5;width:220px;margin:0 auto 22px}

/* about */
.about p{position:absolute;left:210px;top:1150px;width:780px;text-align:center;font-size:15px;line-height:1.75;color:var(--ink)}
.features{position:absolute;left:150px;top:1290px;width:900px;display:flex;justify-content:space-between}
.feature{display:flex;align-items:center;gap:14px;font-size:13px;font-weight:700;line-height:1.3;text-transform:uppercase;color:var(--navy)}
.feature .ring{width:60px;height:60px;border:2px solid var(--orange);border-radius:50%;display:flex;align-items:center;justify-content:center}

/* why */
.why{left:0;top:1480px;width:1200px;height:580px;background:var(--pale);overflow:hidden}
.why-art{position:absolute;left:590px;top:-40px;width:760px;height:660px;border-radius:50%;background:radial-gradient(circle at 40% 45%,#4fd0f5 0%,#1e7be0 45%,#0a3f95 100%)}
.why h2{position:absolute;left:130px;top:100px;font-size:44px;font-weight:500;color:var(--blue)}
.why p{position:absolute;left:130px;top:190px;width:420px;font-size:15px;line-height:1.7}
.why ul{position:absolute;left:130px;top:300px;list-style:none}
.why li{display:flex;align-items:center;gap:14px;font-size:15px;margin-bottom:18px;color:var(--ink)}
.tick{width:24px;height:24px;border-radius:50%;background:var(--orange);display:flex;align-items:center;justify-content:center}

/* testimonials */
.testimonials{left:0;top:2060px;width:1200px;height:510px;background:var(--orange);overflow:hidden}
.testimonials h2{position:absolute;top:70px;width:1200px;text-align:center;color:var(--white);font-size:42px;font-weight:500}
.t-card{position:absolute;top:180px;width:420px;height:220px;background:var(--white);padding:30px 30px 0 30px;display:flex;gap:22px}
.avatar{flex:none;width:76px;height:76px;border-radius:50%;background:linear-gradient(#c9d4df,#8496a8);margin-top:-58px;border:4px solid var(--white)}
.t-card p{font-size:14px;line-height:1.6;color:var(--muted)}
.t-card strong{display:block;font-size:13px;margin-top:12px;color:var(--ink)}
.stars{color:var(--orange);font-size:16px;letter-spacing:2px}
.quote{position:absolute;right:28px;bottom:26px}
.dots{position:absolute;top:450px;left:570px;display:flex;gap:10px}
.dots span{width:10px;height:10px;border-radius:50%;background:rgba(255,255,255,.55)}
.dots span:first-child{background:var(--white)}

/* blogs */
.blog-hero{position:absolute;left:130px;top:2740px;width:460px;height:380px;background:linear-gradient(150deg,#0d2a57,#b4461e 55%,#0b1836)}
.blog-hero .tag,.blog-card .tag{display:inline-block;background:var(--blue);color:var(--white);font-size:10px;font-weight:700;padding:4px 10px}
.blog-hero .caption{position:absolute;left:30px;bottom:30px;width:400px;color:var(--white)}
.blog-hero h3{font-size:20px;line-height:1.35;margin:12px 0 8px}
.blog-hero p{font-size:12px;line-height:1.6;opacity:.85}
.blog-thumb{position:absolute;left:610px;width:220px;height:180px}
.blog-card{position:absolute;left:836px;width:230px;height:180px;border:1px solid #9cc3ef;padding:16px 18px}
.blog-card h3{font-size:15px;line-height:1.35;margin:10px 0 6px;color:var(--navy)}
.blog-card p{font-size:11px;line-height:1.5;color:var(--muted)}
.read{display:block;margin-top:8px;font-size:11px;font-weight:700;color:var(--blue)}

/* faq */
.faq{left:0;top:3200px;width:1200px;height:730px;background:var(--pale)}
.faq-open{position:absolute;left:160px;top:160px;width:900px;height:196px;background:var(--white);border:1px solid var(--line);padding:22px 26px}
.faq-open h3{font-size:17px;color:var(--navy);font-family:"Open Sans",sans-serif;font-weight:700;margin-bottom:14px}
.faq-open p{font-size:13px;line-height:1.65;color:var(--muted)}
.faq-item{position:absolute;left:160px;width:900px;height:60px;background:var(--white);border:1px solid var(--line);display:flex;align-items:center;justify-content:space-between;padding:0 26px;font-size:15px;font-weight:600;color:var(--navy)}
.toggle{width:24px;height:24px;border:1.5px solid #9aa5b1;border-radius:50%;display:flex;align-items:center;justify-content:center}

/* contact */
.contact{left:0;top:3960px;width:1200px;height:480px;background:var(--blue);overflow:hidden}
.contact-side{position:absolute;left:0;top:0}
.contact h2{position:absolute;left:130px;top:130px;width:340px;color:var(--white);font-size:36px;font-weight:500;line-height:1.2}
.contact .lead{position:absolute;left:130px;top:240px;width:330px;color:var(--white);font-size:14px;line-height:1.65}
.field{position:absolute;background:var(--white);height:34px;width:250px;font-size:12px;color:var(--muted);padding:9px 14px}
.field.wide{width:510px;height:86px}
.contact .btn{position:absolute;left:550px;top:250px;border-radius:2px;background:var(--orange);font-size:12px;padding:11px 28px}

/* footer */
.footer-logo{position:absolute;left:130px;top:4500px;color:var(--blue);font-size:52px}
.social{position:absolute;left:140px;top:4600px;display:flex;gap:10px}
.social span{width:36px;height:36px;border-radius:50%;background:var(--orange)}
.f-col{position:absolute;top:4490px}
.f-col h4{font-family:"Ubuntu",sans-serif;font-size:20px;font-weight:500;color:var(--blue);margin-bottom:16px}
.f-col li{list-style:none;font-size:13px;color:var(--ink);margin-bottom:12px;display:flex;align-items:center;gap:12px}
.f-col .ic{flex:none;width:26px;height:26px;border-radius:50%;background:#8d96a1;display:flex;align-items:center;justify-content:center}
.rule{position:absolute;left:0;top:4770px;width:1200px;height:1px;background:var(--line)}
.copyright{position:absolute;top:4790px;width:1200px;text-align:center;font-size:12px;color:var(--muted)}
</style>
</head>
<body>

<header class="abs hero">
  <div class="hero-art" role="img" aria-label="Glowing digital chain link over a dark blue binary code background"></div>
  <svg class="hero-curve" width="1200" height="240" viewBox="0 0 1200 240"><path d="M0 120 Q600 320 1200 120 L1200 240 L0 240Z" fill="#fff"/></svg>
  <nav class="nav">
    <span class="brand">quillink</span>
    <ul>
      <li><a href="#">HOME</a></li><li><a href="#">ABOUT US</a></li><li><a href="#">SERVICES</a></li>
      <li><a href="#">TESTIMONIALS</a></li><li><a href="#">FAQ</a></li><li><a href="#">CONTACT</a></li>
    </ul>
  </nav>
  <p class="hero-kicker">The Real done for you link</p>
  <h1 class="hero-title">quillink links</h1>
  <a class="btn" href="#">GET STARTED</a>
</header>

<section>
  <div class="service blue" style="left:120px;top:640px">
    <svg width="44" height="44" viewBox="0 0 44 44" fill="none" stroke="#fff" stroke-width="2"><rect x="6" y="6" width="32" height="32" rx="3"/><path d="M6 14h32M13 22h18M13 29h12"/></svg>
    <h3>Premium Links</h3>
    <p>Lorem ipsum dolor sit amet, consectetur adipiscing elit sed do eiusmod</p>
    <svg width="22" height="14" viewBox="0 0 22 14" fill="none" stroke="#fff" stroke-width="3"><path d="M2 2l9 9 9-9"/></svg>
  </div>
  <div class="service orange" style="left:415px;top:605px">
    <svg width="48" height="48" viewBox="0 0 48 48" fill="none" stroke="#fff" stroke-width="2"><rect x="6" y="9" width="36" height="32" rx="3"/><path d="M6 18h36M15 5v8M33 5v8M14 26h6M28 26h6M14 33h6M28 33h6"/></svg>
    <h3>Monthly Links<br>Subscription</h3>
    <p>Lorem ipsum dolor sit amet, consectetur adipiscing elit sed do eiusmod</p>
    <svg width="22" height="14" viewBox="0 0 22 14" fill="none" stroke="#fff" stroke-width="3"><path d="M2 2l9 9 9-9"/></svg>
  </div>
  <div class="service blue" style="left:760px;top:640px">
    <svg width="44" height="44" viewBox="0 0 44 44" fill="none" stroke="#fff" stroke-width="2.5"><rect x="5" y="18" width="20" height="10" rx="5" transform="rotate(-45 15 23)"/><rect x="19" y="16" width="20" height="10" rx="5" transform="rotate(-45 29 21)"/></svg>
    <h3>Link Insertions</h3>
    <p>Lorem ipsum dolor sit amet, consectetur adipiscing elit sed do eiusmod</p>
    <svg width="22" height="14" viewBox="0 0 22 14" fill="none" stroke="#fff" stroke-width="3"><path d="M2 2l9 9 9-9"/></svg>
  </div>
</section>

<section class="about">
  <h2 class="section-title" style="top:1050px">About <span class="accent">quillink</span></h2>
  <p>Lorem ipsum dolor sit amet, consectetur adipiscing elit, sed do eiusmod tempor incididunt ut labore et dolore magna aliqua. Ut enim ad minim veniam, quis nostrud exercitation ullamco laboris nisi ut aliquip ex ea commodo consequat. Duis aute irure dolor in reprehenderit in voluptate</p>
  <div class="features">
    <div class="feature"><span class="ring"><svg width="28" height="28" viewBox="0 0 28 28" fill="none" stroke="#f7931e" stroke-width="2"><circle cx="14" cy="11" r="7"/><path d="M9 17l-2 9 7-4 7 4-2-9"/></svg></span>Quality over<br>quantity</div>
    <div class="feature"><span class="ring"><svg width="28" height="28" viewBox="0 0 28 28" fill="none" stroke="#f7931e" stroke-width="2"><rect x="3" y="7" width="22" height="15" rx="2"/><path d="M3 12h22"/></svg></span>One off link<br>payments</div>
    <div class="feature"><span class="ring"><svg width="28" height="28" viewBox="0 0 28 28" fill="none" stroke="#f7931e" stroke-width="2"><circle cx="14" cy="14" r="4"/><path d="M14 3v6M14 19v6M3 14h6M19 14h6M6 6l4 4M18 18l4 4M22 6l-4 4M10 18l-4 4"/></svg></span>Lifetime<br>link gurantee</div>
    <div class="feature"><span class="ring"><svg width="28" height="28" viewBox="0 0 28 28" fill="none" stroke="#f7931e" stroke-width="2"><rect x="4" y="4" width="20" height="20" rx="2"/><path d="M9 14l4 4 7-8"/></svg></span>Lifetime<br>link gurantee</div>
  </div>
</section>

<section class="abs why">
  <div class="why-art" role="img" aria-label="Isometric laptop with glowing data network illustration"></div>
  <h2>Why <span class="accent">quillink</span></h2>
  <p>Lorem ipsum dolor sit amet, consectetur adipiscing elit, sed do eiusmod tempor incididunt ut labore et dolore magna aliqua. Ut enim ad minim veniam nostrud exercit</p>
  <ul>
    <li><span class="tick"><svg width="12" height="10" viewBox="0 0 12 10" fill="none" stroke="#fff" stroke-width="2"><path d="M1 5l3.5 3.5L11 1"/></svg></span>Aquis nostrud exercitation</li>
    <li><span class="tick"><svg width="12" height="10" viewBox="0 0 12 10" fill="none" stroke="#fff" stroke-width="2"><path d="M1 5l3.5 3.5L11 1"/></svg></span>ullamco laboris nisi ut aliquip</li>
    <li><span class="tick"><svg width="12" height="10" viewBox="0 0 12 10" fill="none" stroke="#fff" stroke-width="2"><path d="M1 5l3.5 3.5L11 1"/></svg></span>Ex ea commodo</li>
    <li><span class="tick"><svg width="12" height="10" viewBox="0 0 12 10" fill="none" stroke="#fff" stroke-width="2"><path d="M1 5l3.5 3.5L11 1"/></svg></span>Duis aute irure dolor</li>
  </ul>
</section>

<section class="abs testimonials">
  <h2>Testimonials</h2>
  <article class="t-card" style="left:150px">
    <div class="avatar" role="img" aria-label="Client portrait"></div>
    <div><p>Lorem ipsum dolor sit amet, consectetur adipiscing elit, sed do eiusmod tempor incididunt ut labore et dolore magna aliqua. Ut enim ad minim veniam</p><strong>MARLO PENRICK</strong><span class="stars">★★★★★</span></div>
    <svg class="quote" width="44" height="30" viewBox="0 0 44 30" fill="#d7dde4"><path d="M2 30V16C2 7 7 2 16 1v6c-5 1-7 4-7 9h7v14zM26 30V16c0-9 5-14 14-15v6c-5 1-7 4-7 9h7v14z"/></svg>
  </article>
  <article class="t-card" style="left:610px">
    <div class="avatar" role="img" aria-label="Client portrait"></div>
    <div><p>Lorem ipsum dolor sit amet, consectetur adipiscing elit, sed do eiusmod tempor incididunt ut labore et dolore magna aliqua. Ut enim ad minim veniam</p><strong>MARLO PENRICK</strong><span class="stars">★★★★★</span></div>
    <svg class="quote" width="44" height="30" viewBox="0 0 44 30" fill="#d7dde4"><path d="M2 30V16C2 7 7 2 16 1v6c-5 1-7 4-7 9h7v14zM26 30V16c0-9 5-14 14-15v6c-5 1-7 4-7 9h7v14z"/></svg>
  </article>
  <article class="t-card" style="left:1080px;opacity:.8">
    <div class="avatar" role="img" aria-label="Client portrait"></div>
    <div><p>Lorem ipsum dolor sit amet, consectetur adipiscing elit, sed do eiusmod tempor</p><strong>MARLO PENRICK</strong><span class="stars">★★★★★</span></div>
  </article>
  <div class="dots"><span></span><span></span><span></span></div>
</section>

<section>
  <h2 class="section-title" style="top:2630px">Latest <span class="accent">Blogs</span></h2>
  <article class="blog-hero" role="img" aria-label="Hand touching glowing digital data chart">
    <div class="caption"><span class="tag">10 JAN 2020</span><h3>Lorem ipsum dolor sit amet, consectetur adipiscing elit, sed do eiusmod tempor</h3><p>Lorem ipsum dolor sit amet, consectetur adipiscing elit, sed do eiusmod tempor incididunt ut labore et dolore magna aliqua.</p></div>
  </article>
  <div class="blog-thumb" style="top:2740px;background:linear-gradient(135deg,#3a2a7a,#8fb6ff 50%,#1b1c4e)" role="img" aria-label="Hand reaching toward glowing network"></div>
  <article class="blog-card" style="top:2740px"><span class="tag">10 JAN 2020</span><h3>Lorem ipsum dolor sit amet, consectetur</h3><p>Lorem ipsum dolor sit amet, sed do eiusmod tempor</p><span class="read">READ MORE</span></article>
  <div class="blog-thumb" style="top:2940px;background:linear-gradient(135deg,#0b2246,#3d7fc9 55%,#07162f)" role="img" aria-label="Server room with blue lights"></div>
  <article class="blog-card" style="top:2940px"><span class="tag">10 JAN 2020</span><h3>Lorem ipsum dolor sit amet, consectetur</h3><p>Lorem ipsum dolor sit amet, sed do eiusmod tempor</p><span class="read">READ MORE</span></article>
</section>

<section class="abs faq">
  <h2 class="section-title" style="top:80px">Frequently Asked <span class="accent">Questions</span></h2>
  <div class="faq-open">
    <h3>Lorem ipsum dolor sit amet, consectetur adipiscing elit ?</h3>
    <p>Sed ut perspiciatis unde omnis iste natus error sit voluptatem accusantium doloremque laudantium, totam rem aperiam, eaque ipsa quae ab illo inventore veritatis et quasi architecto beatae vitae dicta sunt explicabo. Nemo enim ipsam voluptatem quia voluptas sit aspernatur aut odit aut fugit, sed quia consequuntur magni dolores eos.</p>
    <span class="read">READ MORE</span>
    <span class="toggle" style="position:absolute;right:22px;top:20px"><svg width="10" height="10" viewBox="0 0 10 10" stroke="#6b7480" stroke-width="1.6"><path d="M2 2l6 6M8 2l-6 6"/></svg></span>
  </div>
  <div class="faq-item" style="top:380px">Sed ut perspiciatis unde omnis iste natus ?<span class="toggle"><svg width="10" height="6" viewBox="0 0 10 6" fill="none" stroke="#6b7480" stroke-width="1.6"><path d="M1 1l4 4 4-4"/></svg></span></div>
  <div class="faq-item" style="top:456px">Error sit voluptatem accusantium doloremque laudantium ?<span class="toggle"><svg width="10" height="6" viewBox="0 0 10 6" fill="none" stroke="#6b7480" stroke-width="1.6"><path d="M1 1l4 4 4-4"/></svg></span></div>
  <div class="faq-item" style="top:532px">Totam rem aperiam, eaque ipsa quae ab illo inventore ?<span class="toggle"><svg width="10" height="6" viewBox="0 0 10 6" fill="none" stroke="#6b7480" stroke-width="1.6"><path d="M1 1l4 4 4-4"/></svg></span></div>
  <div class="faq-item" style="top:608px">Veritatis et quasi architecto beatae vitae dicta ?<span class="toggle"><svg width="10" height="6" viewBox="0 0 10 6" fill="none" stroke="#6b7480" stroke-width="1.6"><path d="M1 1l4 4 4-4"/></svg></span></div>
</section>

<section class="abs contact">
  <svg class="contact-side" width="620" height="480" viewBox="0 0 620 480" role="img" aria-label="Orange tinted abstract light background">
    <defs><linearGradient id="warm" x1="0" y1="0" x2="1" y2="1"><stop offset="0" stop-color="#f7931e"/><stop offset="1" stop-color="#e5690c"/></linearGradient></defs>
    <path d="M0 0H460Q640 240 470 480H0Z" fill="url(#warm)"/>
  </svg>
  <h2>Fill Our Contact form below</h2>
  <p class="lead">Lorem ipsum dolor sit amet, consectetur adipiscing elit, sed do eiusmod tempor incididunt ut labore et dolore magna.</p>
  <div class="field" style="left:550px;top:70px">Name*</div>
  <div class="field" style="left:810px;top:70px">Company</div>
  <div class="field" style="left:550px;top:114px">Email address*</div>
  <div class="field" style="left:810px;top:114px">Phone</div>
  <div class="field wide" style="left:550px;top:158px">Write message</div>
  <a class="btn" href="#">SEND MESSAGE</a>
</section>

<footer>
  <span class="brand footer-logo">quillink</span>
  <div class="social"><span></span><span></span><span></span><span></span></div>
  <div class="f-col" style="left:430px">
    <h4>Contact Us</h4>
    <ul>
      <li><span class="ic"><svg width="12" height="14" viewBox="0 0 12 14" fill="#fff"><path d="M6 0a5 5 0 0 0-5 5c0 4 5 9 5 9s5-5 5-9a5 5 0 0 0-5-5zm0 7a2 2 0 1 1 0-4 2 2 0 0 1 0 4z"/></svg></span>12 Quill Lane, Suite 4,<br>Harbor City 10020</li>
      <li><span class="ic"><svg width="12" height="12" viewBox="0 0 12 12" fill="#fff"><path d="M2 0l2 3-1.5 1.5a8 8 0 0 0 5 5L9 8l3 2-1 2C5 12 0 7 0 1z"/></svg></span>Phone : 555-0148</li>
      <li><span class="ic"><svg width="12" height="10" viewBox="0 0 12 10" fill="none" stroke="#fff" stroke-width="1.4"><rect x=".7" y=".7" width="10.6" height="8.6"/><path d="M1 1l5 4 5-4"/></svg></span>Email: info@quillink.com</li>
    </ul>
  </div>
  <div class="f-col" style="left:730px">
    <h4>Information</h4>
    <ul><li>About Us</li><li>Features</li><li>Services</li><li>Testimonials</li></ul>
  </div>
  <div class="f-col" style="left:945px">
    <h4>Other links</h4>
    <ul><li>FAQ</li><li>Privacy Policy</li><li>Blogs</li><li>Contact Us</li></ul>
  </div>
  <div class="rule"></div>
  <p class="copyright">Copyright 2020 - quillink. All Right Reserved</p>
</footer>

</body>
</html>
```